I need a website, primarily a landing page, for my company, Morrow Vantage. A sales training and cons

I need a web design/landing page for a new sales training and consulting company, morrow vantage. We perform "sales experiments" aimed at each individual or team, where we assist in helping them identify their strengths, through a series of "sales experiments" that we can tailor based on the individual and what they're trying to accomplish.

```html
<!DOCTYPE html>
<html lang="en">
<head>
<meta charset="utf-8">
<title>Morrow Vantage — Sales Training and Consulting</title>
<link href="https://fonts.googleapis.com/css2?family=Montserrat:wght@400;500;600;700&family=Lato:wght@400;700&display=swap" rel="stylesheet">
<style>
:root{
  --blue:#2a63aa;
  --blue-deep:#1f4f8f;
  --blue-band:#2f6fb6;
  --ink:#333;
  --muted:#6a6a6a;
  --white:#fff;
  --grey-btn:#8c8a88;
}
*{margin:0;padding:0;box-sizing:border-box}
html,body{width:1200px;height:3516px;overflow:hidden}
body{font-family:'Lato',sans-serif;color:var(--ink);background:var(--white);position:relative}
section,header,footer{position:absolute;left:0;width:1200px;overflow:hidden}
.abs{position:absolute}
.heading{font-family:'Montserrat',sans-serif;font-weight:700;text-transform:uppercase}

/* Hero */
.hero{top:0;height:715px}
.hero-photo{position:absolute;inset:0;background:linear-gradient(180deg,#8c96a2 0%,#a5aeb8 40%,#7d8894 75%,#5e6975 100%)}
.hero-shade{position:absolute;inset:0;background:rgba(20,35,55,.28)}
.brand{left:105px;top:24px;width:150px;display:flex;flex-direction:column;align-items:center;color:var(--white)}
.brand-mark{width:46px;height:46px;border-radius:50%;border:3px solid var(--white);margin-bottom:10px}
.brand-name{font-family:'Montserrat',sans-serif;font-weight:700;font-size:17px;letter-spacing:.3px;line-height:1;white-space:nowrap}
.topbar{right:80px;top:26px;display:flex;gap:34px;color:var(--white);font-family:'Montserrat',sans-serif;font-size:15px;align-items:center}
.topbar span{display:flex;align-items:center;gap:8px}
.nav{right:82px;top:73px;display:flex;gap:36px;font-family:'Montserrat',sans-serif;font-size:16px;color:var(--white)}
.nav .active{font-weight:700}
.social-rail{left:42px;top:285px;display:flex;flex-direction:column;gap:30px}
.social-rail i{display:block;width:14px;height:14px;border-radius:50%;background:var(--white)}
.follow{left:40px;top:580px;transform:rotate(-90deg);transform-origin:left top;color:var(--white);font-family:'Montserrat',sans-serif;font-size:14px;white-space:nowrap}
.follow-line{left:50px;top:460px;width:2px;height:60px;background:rgba(255,255,255,.6)}
.hero-copy{left:0;width:1200px;top:313px;text-align:center;color:var(--white)}
.hero-copy .pre{font-size:37px;line-height:1}
.hero-copy h1{font-family:'Montserrat',sans-serif;font-weight:700;font-size:58px;line-height:1;margin-top:14px;text-transform:uppercase}
.hero-copy p{font-family:'Montserrat',sans-serif;font-weight:500;font-size:27px;line-height:44px;margin-top:6px}
.btn-primary{left:516px;top:525px;width:170px;height:54px;border-radius:27px;background:var(--blue);color:var(--white);font-family:'Montserrat',sans-serif;font-weight:700;font-size:18px;display:flex;align-items:center;justify-content:center}
.dots{left:1145px;top:388px;display:flex;flex-direction:column;gap:22px;align-items:center}
.dots i{display:block;width:12px;height:12px;border-radius:50%;background:var(--white)}
.dots i.on{width:24px;height:24px;border:3px solid var(--white);background:transparent;position:relative}
.dots i.on::after{content:"";position:absolute;left:4px;top:4px;width:10px;height:10px;border-radius:50%;background:var(--white)}

/* About */
.about{top:715px;height:464px;background:var(--blue-band)}
.about-media{left:112px;top:84px;width:448px;height:298px;background:linear-gradient(135deg,#d9dbdc,#a7a39d 55%,#4a4744)}
.about h2{left:605px;top:86px;font-size:36px;color:var(--white)}
.about p{left:605px;top:140px;width:505px;font-size:15px;line-height:31px;color:var(--white);text-align:justify}
.btn-grey{left:607px;top:319px;width:157px;height:51px;border-radius:26px;background:var(--grey-btn);color:var(--white);font-family:'Montserrat',sans-serif;font-weight:700;font-size:15px;display:flex;align-items:center;justify-content:center;gap:6px}

/* Services */
.services{top:1179px;height:638px;background:var(--white)}
.services h2{left:0;width:1200px;text-align:center;top:70px;font-size:37px;color:var(--blue)}
.services .sub{left:0;width:1200px;text-align:center;top:128px;font-size:29px;color:#444}
.services svg{position:absolute;left:0;top:0}
.svc-label{font-family:'Montserrat',sans-serif;font-weight:600;font-size:17px;fill:var(--blue)}

/* What we have */
.offer{top:1817px;height:672px}
.offer-photo{position:absolute;inset:0;background:linear-gradient(180deg,#4a4a4a,#303030 50%,#444)}
.offer h2{left:0;width:1200px;text-align:center;top:86px;font-size:37px;color:var(--white)}
.card{width:447px;height:186px;background:var(--white);padding:34px 24px 0 107px}
.card svg{position:absolute;left:42px;top:36px}
.card h3{font-family:'Montserrat',sans-serif;font-weight:700;font-size:22px;color:var(--blue);text-transform:uppercase}
.card p{font-size:14px;line-height:27px;color:var(--muted);margin-top:6px}
.card .more{font-family:'Montserrat',sans-serif;font-weight:700;font-size:14px;color:#222;margin-top:6px}

/* Blog */
.blog{top:2489px;height:605px}
.blog h2{left:0;width:1200px;text-align:center;top:58px;font-size:37px;color:var(--blue)}
.post{top:155px;width:327px}
.post-photo{height:195px}
.post .date{position:absolute;left:17px;top:178px;height:33px;padding:0 12px;background:var(--blue-deep);color:var(--white);font-size:13px;display:flex;align-items:center;gap:6px}
.post h3{margin-top:38px;font-family:'Montserrat',sans-serif;font-weight:700;font-size:18px;color:var(--blue);text-transform:uppercase}
.post p{margin-top:12px;font-size:11.5px;line-height:24px;color:var(--ink)}
.post .more{margin-top:14px;font-family:'Montserrat',sans-serif;font-weight:700;font-size:13px;color:var(--blue)}

/* Footer */
.footer{top:3094px;height:422px}
.footer-photo{position:absolute;inset:0;background:linear-gradient(135deg,#3f77b8,#2a5f9f 50%,#1f4e88)}
.footer .brand{left:500px;top:30px;width:200px}
.footer .brand .brand-mark{width:64px;height:64px;margin-bottom:16px}
.footer .brand-name{font-size:21px}
.contact{left:0;width:1200px;top:206px;display:flex;justify-content:center;gap:50px;color:var(--white);font-family:'Montserrat',sans-serif;font-size:16px}
.contact span{display:flex;align-items:center;gap:10px}
.social{left:0;width:1200px;top:255px;display:flex;justify-content:center;gap:13px}
.social i{display:block;width:44px;height:44px;border-radius:50%;background:rgba(255,255,255,.28)}
.links{left:0;width:1200px;top:331px;text-align:center;color:var(--white);font-family:'Montserrat',sans-serif;font-size:16px;word-spacing:2px}
.links b{font-weight:400;margin:0 10px}
.copy{left:0;width:1200px;top:380px;text-align:center;color:var(--white);font-family:'Montserrat',sans-serif;font-size:14px}
</style>
</head>
<body>

<header class="hero">
  <div class="hero-photo" role="img" aria-label="Business team meeting around a conference table in a bright office"></div>
  <div class="hero-shade"></div>
  <div class="abs brand">
    <div class="brand-mark"></div>
    <div class="brand-name">MORROW VANTAGE</div>
  </div>
  <div class="abs topbar">
    <span><svg width="14" height="14" viewBox="0 0 24 24"><path fill="#fff" d="M6.6 10.8a15 15 0 0 0 6.6 6.6l2.2-2.2c.3-.3.7-.4 1-.2 1.1.4 2.3.6 3.6.6.6 0 1 .4 1 1V20c0 .6-.4 1-1 1A17 17 0 0 1 3 4c0-.6.4-1 1-1h3.5c.6 0 1 .4 1 1 0 1.3.2 2.5.6 3.6.1.3 0 .7-.2 1z"/></svg>555-014-2290</span>
    <span><svg width="15" height="12" viewBox="0 0 24 18"><rect width="24" height="18" rx="2" fill="#fff"/><path d="M1 2l11 8 11-8" stroke="#8c96a2" stroke-width="2" fill="none"/></svg>info@morrowvantage.com</span>
    <span><svg width="16" height="11"><rect width="16" height="11" fill="#c33"/><rect y="4" width="16" height="3" fill="#fff"/><rect x="6" width="3" height="11" fill="#fff"/></svg>English ▾</span>
  </div>
  <nav class="abs nav">
    <span class="active">Home</span><span>About Us</span><span>Services</span><span>News</span><span>Our Blog</span><span>Contacts Us</span>
  </nav>
  <div class="abs social-rail"><i></i><i></i><i></i><i></i></div>
  <div class="abs follow-line"></div>
  <div class="abs follow">Follow Us</div>
  <div class="abs hero-copy">
    <div class="pre heading">Welcome to</div>
    <h1>Morrow Vantage</h1>
    <p>Sed ut perspiciatis unde omnis iste natus error sit<br>voluptatem accusantium doloremque</p>
  </div>
  <div class="abs btn-primary">Read More</div>
  <div class="abs dots"><i></i><i class="on"></i><i></i></div>
</header>

<section class="about">
  <div class="abs about-media" role="img" aria-label="Presenter at a flip chart explaining sales figures to a seated team"></div>
  <svg class="abs" style="left:306px;top:198px" width="60" height="60" viewBox="0 0 60 60"><circle cx="30" cy="30" r="27" fill="none" stroke="#fff" stroke-width="3"/><path d="M24 18l18 12-18 12z" fill="#fff"/></svg>
  <h2 class="abs heading">About Us</h2>
  <p class="abs">Sed ut perspiciatis unde omnis iste natus error sit voluptatem accusantium doloremque laudantium, totam rem aperiam, eaque ipsa quae ab illo inventore veritatis et quasi architecto beatae vitae dicta sunt explicabo. Lorem ipsum dolor sit amet, consectetur adipiscing elit, sed do eiusmod.</p>
  <div class="abs btn-grey">Read More <svg width="14" height="14" viewBox="0 0 14 14"><circle cx="7" cy="7" r="7" fill="#fff"/><path d="M5.5 4l3 3-3 3" stroke="#8c8a88" stroke-width="2" fill="none"/></svg></div>
</section>

<section class="services">
  <h2 class="abs heading">Morrow Vantage Services</h2>
  <div class="abs sub">Training and Consulting Company</div>
  <svg width="1200" height="638" viewBox="0 0 1200 638">
    <circle cx="600" cy="638" r="274" fill="#e5e5e5"/>
    <circle cx="600" cy="638" r="211" fill="#2a63aa"/>
    <circle cx="600" cy="638" r="382" fill="none" stroke="#777" stroke-width="1.5" stroke-dasharray="6 6"/>
    <text x="600" y="570" text-anchor="middle" class="svc-label" style="fill:#fff;font-size:20px;font-weight:700">MORROW VANTAGE</text>
    <g fill="#fff" stroke="#e2e2e2" stroke-width="4">
      <circle cx="448" cy="284" r="32"/><circle cx="757" cy="284" r="32"/>
      <circle cx="295" cy="408" r="32"/><circle cx="919" cy="408" r="32"/>
      <circle cx="213" cy="558" r="32"/><circle cx="996" cy="558" r="32"/>
    </g>
    <g fill="none" stroke="#2a63aa" stroke-width="2">
      <rect x="436" y="272" width="24" height="18" rx="2"/><path d="M440 296h16"/>
      <circle cx="757" cy="282" r="10"/><path d="M757 272v10l6 4"/>
      <rect x="283" y="396" width="18" height="24"/><path d="M287 412v4M292 406v10M297 402v14"/>
      <path d="M907 414l18-12v20zM903 410h4v8h-4z"/>
      <rect x="201" y="546" width="22" height="24" rx="2"/><path d="M206 554h12M206 560h12"/>
      <rect x="984" y="546" width="24" height="18"/><path d="M988 570h16M996 564v6"/>
    </g>
    <text x="394" y="292" text-anchor="end" class="svc-label">CONSULTING</text>
    <text x="808" y="292" class="svc-label">STRATEGY</text>
    <text x="241" y="414" text-anchor="end" class="svc-label">ANALYTICS</text>
    <text x="963" y="414" class="svc-label">Marketing</text>
    <text x="178" y="564" text-anchor="end" class="svc-label">ADVISORY</text>
    <text x="1043" y="564" class="svc-label">TRAINING</text>
  </svg>
</section>

<section class="offer">
  <div class="offer-photo" role="img" aria-label="Dimmed office scene with people working at desks"></div>
  <h2 class="abs heading">What We Have</h2>
  <div class="abs card" style="left:134px;top:175px">
    <svg width="46" height="46" viewBox="0 0 46 46" fill="none" stroke="#2a63aa" stroke-width="2.5"><circle cx="20" cy="14" r="8"/><path d="M6 42c0-10 6-16 14-16s14 6 14 16"/></svg>
    <h3>Expert Consultant</h3><p>Sed ut perspiciatis unde omnis iste natus error sit voluptatem accusantium doloremque</p><div class="more">Read More</div>
  </div>
  <div class="abs card" style="left:619px;top:175px">
    <svg width="46" height="46" viewBox="0 0 46 46" fill="none" stroke="#2a63aa" stroke-width="2.5"><path d="M23 4l18 8v10c0 11-8 18-18 21C13 40 5 33 5 22V12z"/><path d="M15 23l6 6 10-11"/></svg>
    <h3>Risk Management</h3><p>Sed ut perspiciatis unde omnis iste natus error sit voluptatem accusantium doloremque</p><div class="more">Read More</div>
  </div>
  <div class="abs card" style="left:134px;top:398px">
    <svg width="46" height="46" viewBox="0 0 46 46" fill="none" stroke="#2a63aa" stroke-width="2.5"><circle cx="23" cy="23" r="18"/><path d="M5 23h36M23 5c-8 10-8 26 0 36M23 5c8 10 8 26 0 36"/></svg>
    <h3>Global Business</h3><p>Sed ut perspiciatis unde omnis iste natus error sit voluptatem accusantium doloremque</p><div class="more">Read More</div>
  </div>
  <div class="abs card" style="left:619px;top:398px">
    <svg width="46" height="46" viewBox="0 0 46 46" fill="none" stroke="#2a63aa" stroke-width="2.5"><rect x="8" y="5" width="30" height="36" rx="2"/><path d="M14 14h18M14 21h18M14 28h12"/></svg>
    <h3>Marketing Plan</h3><p>Sed ut perspiciatis unde omnis iste natus error sit voluptatem accusantium doloremque</p><div class="more">Read More</div>
  </div>
</section>

<section class="blog">
  <h2 class="abs heading">Our Blog</h2>
  <article class="abs post" style="left:77px">
    <div class="post-photo" role="img" aria-label="Two colleagues reviewing work on a laptop" style="background:linear-gradient(135deg,#e9ecef,#b9c2cc 60%,#6f7d8c)"></div>
    <div class="date"><svg width="12" height="12"><rect width="12" height="12" rx="1" fill="#fff"/></svg>Oct 23 2018</div>
    <h3>Sed ut perspiciatis und</h3>
    <p>Sed ut perspiciatis unde omnis iste natus error sit voluptatem accusantium doloremque laudantium, totam rem aperiam, eaque ipsa quae ab illo</p>
    <div class="more">READ MORE</div>
  </article>
  <article class="abs post" style="left:436px">
    <div class="post-photo" role="img" aria-label="Hands pointing at printed charts on a desk" style="background:linear-gradient(135deg,#f1f3f5,#c7ced6 55%,#7e8a97)"></div>
    <div class="date"><svg width="12" height="12"><rect width="12" height="12" rx="1" fill="#fff"/></svg>Oct 23 2018</div>
    <h3>Sed ut perspiciatis und</h3>
    <p>Sed ut perspiciatis unde omnis iste natus error sit voluptatem accusantium doloremque laudantium, totam rem aperiam, eaque ipsa quae ab illo</p>
    <div class="more">READ MORE</div>
  </article>
  <article class="abs post" style="left:795px">
    <div class="post-photo" role="img" aria-label="Team analysing reports around a meeting table" style="background:linear-gradient(135deg,#3c4a58,#6f7b86 50%,#b9bfc4)"></div>
    <div class="date"><svg width="12" height="12"><rect width="12" height="12" rx="1" fill="#fff"/></svg>Oct 23 2018</div>
    <h3>Sed ut perspiciatis und</h3>
    <p>Sed ut perspiciatis unde omnis iste natus error sit voluptatem accusantium doloremque laudantium, totam rem aperiam, eaque ipsa quae ab illo</p>
    <div class="more">READ MORE</div>
  </article>
</section>

<footer class="footer">
  <div class="footer-photo" role="img" aria-label="Blue-tinted handshake over a desk"></div>
  <div class="abs brand">
    <div class="brand-mark"></div>
    <div class="brand-name">MORROW VANTAGE</div>
  </div>
  <div class="abs contact">
    <span><svg width="16" height="16" viewBox="0 0 24 24"><path fill="#fff" d="M22 2L2 10l8 3 3 9z"/></svg>120 Harbor Lane Portsmouth</span>
    <span><svg width="15" height="15" viewBox="0 0 24 24"><path fill="#fff" d="M6.6 10.8a15 15 0 0 0 6.6 6.6l2.2-2.2c.3-.3.7-.4 1-.2 1.1.4 2.3.6 3.6.6.6 0 1 .4 1 1V20c0 .6-.4 1-1 1A17 17 0 0 1 3 4c0-.6.4-1 1-1h3.5c.6 0 1 .4 1 1 0 1.3.2 2.5.6 3.6.1.3 0 .7-.2 1z"/></svg>Phone: +(555) 014-2290</span>
    <span><svg width="16" height="12" viewBox="0 0 24 18"><rect width="24" height="18" rx="2" fill="#fff"/><path d="M1 2l11 8 11-8" stroke="#2a5f9f" stroke-width="2" fill="none"/></svg>Email: info@morrowvantage.com</span>
  </div>
  <div class="abs social"><i></i><i></i><i></i><i></i><i></i></div>
  <div class="abs links">Home<b>|</b>About Us<b>|</b>Our Service<b>|</b>Latest News<b>|</b>Our Blog<b>|</b>Contact us</div>
  <div class="abs copy">Copyright © 2018. All Rights Reserved.</div>
</footer>

</body>
</html>
```